Meridale Partners Website

Meridale Partners (MP) provide Analytics & Enterprise Performance Management (EPM) advisory & consultancy services. We are passionate about data and making a difference for our clients by working in partnership with them, helping them on their journey to becoming an Meridale Partner. We deliver insights which give our clients a competitive edge and a much deeper understanding of their organisation.

We need a website which shows who we are, what we do and how we do it.

www.meridale-partners.example is our very basic website at the moment. We want to completely revamp it with a corporate look

```html
<!DOCTYPE html>
<html lang="en">
<head>
<meta charset="utf-8">
<title>Meridale Partners</title>
<link href="https://fonts.googleapis.com/css2?family=Lato:wght@400;700;900&display=swap" rel="stylesheet">
<style>
:root{
  --navy:#1d3649;
  --navy-dark:#14263a;
  --orange:#e8833a;
  --ink:#2a2a2a;
  --muted:#555c63;
  --pale:#e9f2f8;
  --line:#d9dde1;
  --white:#ffffff;
  --black:#0b0b0b;
}
*{box-sizing:border-box;margin:0;padding:0}
html,body{width:1200px;height:3284px;overflow:hidden}
body{position:relative;font-family:"Lato",sans-serif;color:var(--ink);background:var(--white)}
.abs{position:absolute}

/* header */
.site-header{left:0;top:0;width:1200px;height:88px;background:var(--white);z-index:3}
.brand-tab{left:0;top:0;width:300px;height:88px;background:var(--navy)}
.brand{left:40px;top:22px;display:flex;align-items:center;gap:12px;color:var(--white);font-weight:900;font-size:19px;line-height:20px;letter-spacing:.5px}
.brand-dot{width:38px;height:38px;border-radius:50%;border:4px solid var(--white)}
.contact-row{left:580px;top:12px;display:flex;gap:40px;font-size:13px;color:var(--muted)}
.contact-row span{display:flex;align-items:center;gap:8px}
.mini-ico{width:22px;height:22px;border-radius:50%;background:var(--orange);display:inline-flex;align-items:center;justify-content:center}
.main-nav{left:560px;top:50px;display:flex;gap:6px;font-size:15px}
.main-nav a{color:var(--navy);text-decoration:none;padding:6px 14px}
.main-nav a.active{background:var(--navy);color:var(--white)}
.social{left:1018px;top:54px;display:flex;gap:14px}
.social i{display:block;width:20px;height:20px;border-radius:50%;background:var(--navy)}

/* hero */
.hero{left:0;top:88px;width:1200px;height:772px;background:linear-gradient(120deg,#3a4450 0%,#6b6c70 35%,#8c8f93 55%,#3c4f63 100%)}
.hero-shade{left:0;top:88px;width:1200px;height:772px;background:linear-gradient(90deg,rgba(20,38,58,0) 45%,rgba(20,38,58,.55) 100%)}
.hero-copy{left:710px;top:250px;color:var(--white)}
.hero-copy .kicker{font-size:34px;font-weight:700}
.hero-copy h1{font-size:62px;font-weight:900;line-height:64px;margin-top:10px;letter-spacing:1px}
.btn{display:inline-block;background:var(--orange);color:var(--white);font-weight:700;border-radius:8px;text-decoration:none}
.hero-copy .btn{margin-top:44px;font-size:17px;padding:14px 28px}
.dots{left:1142px;top:340px;display:flex;flex-direction:column;gap:14px}
.dots i{display:block;width:12px;height:12px;border-radius:50%;background:var(--white)}
.dots i.on{background:var(--orange)}
.hero-curve{left:0;top:760px}

/* section heads */
.section-title{left:0;width:1200px;display:flex;justify-content:center;align-items:center;gap:24px;font-size:46px;font-weight:400;color:var(--navy);letter-spacing:1px}
.section-title::before,.section-title::after{content:"";width:80px;height:3px;background:var(--navy)}

/* services */
.service{top:1020px;width:290px;height:320px;background:var(--white);border:1px solid var(--line);box-shadow:0 6px 18px rgba(0,0,0,.08);text-align:center;padding:28px 22px 0}
.service h3{font-size:18px;font-weight:700;color:var(--navy);margin-top:18px;line-height:24px}
.service p{font-size:14px;color:var(--muted);line-height:20px;margin-top:14px}
.service .more{position:absolute;left:22px;right:22px;bottom:0;height:62px;border-top:1px solid var(--line);display:flex;align-items:center;justify-content:center;gap:16px;font-size:17px;color:var(--ink)}

/* about */
.about{left:0;top:1440px;width:1200px;height:560px;background:var(--pale)}
.about-photo{left:100px;top:1500px;width:380px;height:380px;border-radius:50%;background:radial-gradient(circle at 45% 45%,#c9b9a8,#6f7a86 70%);border:10px solid var(--white)}
.about-ring{left:84px;top:1484px}
.about-copy{left:540px;top:1510px;width:560px}
.about-copy h2{font-size:48px;font-weight:400;color:var(--navy);letter-spacing:1px;position:relative;padding-left:108px}
.about-copy h2::before{content:"";position:absolute;left:0;top:28px;width:84px;height:3px;background:var(--navy)}
.about-copy .lead{font-size:17px;font-weight:700;line-height:28px;margin-top:28px}
.about-copy .body{font-size:16px;line-height:27px;color:var(--muted);margin-top:18px}
.about-copy .btn{margin-top:28px;font-size:15px;padding:12px 26px}

/* process */
.step{top:2230px;width:320px;text-align:center}
.step .photo{width:280px;height:280px;border-radius:50%;margin:0 auto;position:relative}
.step .num{position:absolute;left:110px;bottom:-26px;width:60px;height:60px;border-radius:50%;background:var(--navy);color:var(--white);border:4px solid var(--white);font-size:20px;font-weight:700;display:flex;align-items:center;justify-content:center}
.step h4{font-size:17px;font-weight:700;color:var(--ink);margin-top:60px;line-height:24px;min-height:48px}
.step p{font-size:15px;line-height:22px;color:var(--muted);margin:22px auto 0;width:230px}

/* footer */
.site-footer{left:0;top:2860px;width:1200px;height:424px;background:var(--black);color:var(--white)}
.f-brand{left:120px;top:2890px;display:flex;align-items:center;gap:12px;font-weight:900;font-size:22px;line-height:24px}
.f-contact{left:120px;top:2990px;display:flex;flex-direction:column;gap:26px;font-size:15px;line-height:22px}
.f-contact div{display:flex;gap:16px;align-items:flex-start}
.f-contact .mini-ico{width:34px;height:34px;flex:none}
.f-head{font-size:16px;font-weight:700;letter-spacing:.5px}
.f-links{left:532px;top:2995px}
.f-links ul{list-style:none;margin-top:16px;font-size:14px;line-height:26px}
.f-news{left:760px;top:2995px;width:330px}
.f-input{margin-top:20px;height:50px;border-radius:25px;background:var(--white);color:#555;font-size:15px;padding:15px 24px}
.f-news .btn{margin-top:16px;border-radius:25px;padding:14px 34px;font-size:15px}
.f-follow{display:flex;align-items:center;gap:12px;margin-top:30px;font-size:15px;font-weight:700}
.f-follow i{display:block;width:30px;height:30px;border-radius:50%;border:2px solid var(--white)}
.f-rule{left:0;top:3228px;width:1200px;height:1px;background:#333}
.copyright{left:0;top:3248px;width:1200px;text-align:center;font-size:14px}
</style>
</head>
<body>

<header class="abs site-header">
  <div class="abs brand-tab"></div>
  <div class="abs brand"><span class="brand-dot"></span><span>MERIDALE<br>PARTNERS</span></div>
  <div class="abs contact-row">
    <span><i class="mini-ico"><svg width="12" height="12" viewBox="0 0 24 24"><path fill="#fff" d="M6.6 10.8a15 15 0 006.6 6.6l2.2-2.2c.3-.3.7-.4 1-.2 1.1.4 2.3.6 3.6.6.6 0 1 .4 1 1V20c0 .6-.4 1-1 1A17 17 0 013 4c0-.6.4-1 1-1h3.5c.6 0 1 .4 1 1 0 1.3.2 2.5.6 3.6.1.3 0 .7-.2 1z"/></svg></i>Call Us: 01 555 0142</span>
    <span><i class="mini-ico"><svg width="12" height="12" viewBox="0 0 24 24"><path fill="#fff" d="M2 5h20v14H2zm2 2v.5l8 5 8-5V7z"/></svg></i>Mail Us: info@meridale-partners.example</span>
  </div>
  <nav class="abs main-nav"><a class="active">Home</a><a>Services</a><a>About Us</a><a>Contact Us</a></nav>
  <div class="abs social"><i></i><i></i></div>
</header>

<section>
  <div class="abs hero" role="img" aria-label="Photo of smiling businessman shaking hands across a desk in a bright office"></div>
  <div class="abs hero-shade"></div>
  <div class="abs hero-copy">
    <div class="kicker">Welcome To</div>
    <h1>MERIDALE<br>PARTNERS</h1>
    <a class="btn">Get A Quote</a>
  </div>
  <div class="abs dots"><i></i><i class="on"></i><i></i></div>
  <svg class="abs hero-curve" width="1200" height="110" viewBox="0 0 1200 110">
    <path d="M0 20 Q600 120 1200 10 L1200 40 Q600 140 0 50Z" fill="#e8833a"/>
    <path d="M0 45 Q600 140 1200 35 L1200 110 L0 110Z" fill="#ffffff"/>
  </svg>
</section>

<section>
  <h2 class="abs section-title" style="top:918px">WHAT WE DO</h2>
  <article class="abs service" style="left:100px">
    <svg width="64" height="56" viewBox="0 0 64 56"><rect x="4" y="4" width="36" height="26" rx="3" fill="none" stroke="#e8833a" stroke-width="3"/><rect x="24" y="22" width="36" height="26" rx="3" fill="#fff" stroke="#e8833a" stroke-width="3"/><path d="M12 30v8l8-8" fill="none" stroke="#e8833a" stroke-width="3"/></svg>
    <h3>ADVISE &amp; ARCHITECT<br>SERVICES</h3>
    <p>Helping our customers understand the art of the possible &amp; safeguarding their investments by overseeing implementations</p>
    <div class="more">Learn More <span>&rarr;</span></div>
  </article>
  <article class="abs service" style="left:455px">
    <svg width="56" height="56" viewBox="0 0 56 56"><rect x="8" y="8" width="40" height="40" fill="none" stroke="#1d3649" stroke-width="3"/><path d="M8 8l40 40M48 8L8 48M28 4v48M4 28h48" stroke="#1d3649" stroke-width="2"/><circle cx="28" cy="28" r="6" fill="#e8833a"/></svg>
    <h3>DESIGN &amp; IMPLEMENT</h3>
    <p>Working with the project management team, through each stage of the project, with clearly defined deliverables &amp; well exercised plans to deliver them</p>
    <div class="more">Learn More <span>&rarr;</span></div>
  </article>
  <article class="abs service" style="left:810px">
    <svg width="56" height="56" viewBox="0 0 56 56"><circle cx="28" cy="28" r="16" fill="none" stroke="#e8833a" stroke-width="6" stroke-dasharray="8 5"/><circle cx="28" cy="28" r="7" fill="#e8833a"/></svg>
    <h3>OPTIMISE &amp; MANAGE</h3>
    <p>Our Managed Services delivers proactive, on-demand support for EPM and Data Analytics environments</p>
    <div class="more">Learn More <span>&rarr;</span></div>
  </article>
</section>

<section>
  <div class="abs about"></div>
  <svg class="abs about-ring" width="412" height="412" viewBox="0 0 412 412"><path d="M40 300 A190 190 0 0 1 206 16" fill="none" stroke="#1d3649" stroke-width="6"/><path d="M372 112 A190 190 0 0 1 206 396" fill="none" stroke="#e8833a" stroke-width="6"/></svg>
  <div class="abs about-photo" role="img" aria-label="Photo of two colleagues reviewing work together at a laptop"></div>
  <div class="abs about-copy">
    <h2>WHO WE ARE</h2>
    <p class="lead">MP are a Data Analytics and EPM company, specialising in the implementation and support of Business Intelligence, EPM and Data Analytics business solutions, both in the Cloud and on-premise.</p>
    <p class="body">Meridale Partners is an exciting start-up in the Data Analytics and EPM space. Founded in 2019, MP specialise in the implementation and support of BI, EPM and Data Analytics business solutions, both in the Cloud and on-premise.</p>
    <a class="btn">Learn More</a>
  </div>
</section>

<section>
  <h2 class="abs section-title" style="top:2090px">HOW IT WORKS</h2>
  <div class="abs step" style="left:80px">
    <div class="photo" role="img" aria-label="Photo of a modern office interior" style="background:linear-gradient(160deg,#a7c0d4,#2f4e6a)"><span class="num">01</span></div>
    <h4>MERIDALE PARTNERS</h4>
    <p>Sed ut perspiciatis unde omnis iste natur sit voluptatem accusantium doloremque laudantium, totam rem aperiam, eaque ipsa</p>
  </div>
  <div class="abs step" style="left:440px">
    <div class="photo" role="img" aria-label="Photo of hands working with charts and reports on a desk" style="background:linear-gradient(160deg,#e7d9c9,#8c7a6a)"><span class="num" style="background:#e8833a">02</span></div>
    <h4>ANALYTICS &amp; ENTERPRISE<br>PERFORMANCE MANAGEMENT</h4>
    <p>Sed ut perspiciatis unde omnis iste natur sit voluptatem accusantium doloremque laudantium, totam rem aperiam, eaque ipsa</p>
  </div>
  <div class="abs step" style="left:800px">
    <div class="photo" role="img" aria-label="Photo of a consultant meeting a client" style="background:linear-gradient(160deg,#d9dde3,#4a5663)"><span class="num">03</span></div>
    <h4>CONSULTANCY SERVICES</h4>
    <p>Sed ut perspiciatis unde omnis iste natur sit voluptatem accusantium doloremque laudantium, totam rem aperiam, eaque ipsa</p>
  </div>
</section>

<footer>
  <div class="abs site-footer"></div>
  <div class="abs f-brand"><span class="brand-dot"></span><span>MERIDALE<br>PARTNERS</span></div>
  <div class="abs f-contact">
    <div><i class="mini-ico"><svg width="16" height="16" viewBox="0 0 24 24"><path fill="#fff" d="M12 2a7 7 0 00-7 7c0 5 7 13 7 13s7-8 7-13a7 7 0 00-7-7zm0 9.5A2.5 2.5 0 1112 6a2.5 2.5 0 010 5.5z"/></svg></i><span>12 Harbour Row,<br>Eastgate, Dublin 4, D04 AB12</span></div>
    <div><i class="mini-ico"><svg width="16" height="16" viewBox="0 0 24 24"><path fill="#fff" d="M6.6 10.8a15 15 0 006.6 6.6l2.2-2.2c.3-.3.7-.4 1-.2 1.1.4 2.3.6 3.6.6.6 0 1 .4 1 1V20c0 .6-.4 1-1 1A17 17 0 013 4c0-.6.4-1 1-1h3.5c.6 0 1 .4 1 1 0 1.3.2 2.5.6 3.6.1.3 0 .7-.2 1z"/></svg></i><span>Call Us:<br>01 555 0142</span></div>
    <div><i class="mini-ico"><svg width="16" height="16" viewBox="0 0 24 24"><path fill="#fff" d="M2 5h20v14H2zm2 2v.5l8 5 8-5V7z"/></svg></i><span>Mail Us:<br>info@meridale-partners.example</span></div>
  </div>
  <div class="abs f-links">
    <div class="f-head">QUICK LINKS</div>
    <ul><li>Home</li><li>About</li><li>Advise &amp; Architect</li><li>Design &amp; Implement</li><li>Optimise &amp; Manage</li><li>Contact</li></ul>
  </div>
  <div class="abs f-news">
    <div class="f-head">SUBSCRIBE NEWSLETTER</div>
    <div class="f-input">Email ID</div>
    <a class="btn">SEND</a>
    <div class="f-follow">FOLLOW US : <i></i><i></i></div>
  </div>
  <div class="abs f-rule"></div>
  <p class="abs copyright">2022 Meridale Partners. All Rights Reserved.</p>
</footer>

</body>
</html>
```